Quorva - corporate Business Card

We need a good look and innovative business card for a new start up company based in Los Angeles called "Quorva". We are in a payment business, including payment card, app, and ewallet. We are expert in online payment and Card not present (CNP) transaction.
We need an innovative, modern business card.

Our logo font is Aero Matics

Target Market(s)

Startup - Bank - Online Payment - Card Manufacturing

Industry/Entity Type

Startup

Contact Information for Business Card

phone: 555 014 7396 - Address: 4172 Marlowe blvd, Alder Vale, NV 89412

Requirements
Must have
• Message: innovative, professional, expert, high tech, trust, online payment expert, security
Nice to have
• no comment
Should not have
• no Comment

```html
<!DOCTYPE html>
<html lang="en">
<head>
<meta charset="utf-8">
<title>Quorva — Business Card</title>
<link rel="stylesheet" href="https://fonts.googleapis.com/css2?family=Open+Sans:wght@400;600;700&display=swap">
<style>
  :root {
    --brand-red: #b5121b;
    --brand-red-bright: #d7263a;
    --card-white: #f7f7f7;
    --ink-grey: #6b6b6b;
    --rule-grey: #d2d2d2;
    --backdrop: #d9dbe0;
  }
  * { box-sizing: border-box; margin: 0; padding: 0; }
  html, body {
    width: 1200px; height: 878px; overflow: hidden;
    background: var(--backdrop);
    font-family: "Open Sans", Arial, sans-serif;
  }
  .canvas { position: relative; width: 1200px; height: 878px; }
  .card {
    position: absolute; top: 290px;
    width: 520px; height: 297px;
    box-shadow: 0 6px 18px rgba(0,0,0,0.18);
  }
  .card--front { left: 60px; background: var(--card-white); }
  .card--back {
    left: 620px;
    background: linear-gradient(135deg, var(--brand-red-bright), #c81c30 55%, var(--brand-red));
  }
  .brand {
    position: absolute; left: 38px; top: 118px;
    display: flex; align-items: center; gap: 10px;
  }
  .brand__dot {
    width: 52px; height: 52px; border-radius: 50%;
    background: var(--brand-red);
  }
  .brand__name {
    font-size: 44px; font-weight: 600; color: var(--brand-red);
    letter-spacing: 1px; line-height: 1;
  }
  .divider {
    position: absolute; left: 292px; top: 92px;
    width: 1px; height: 112px; background: var(--rule-grey);
  }
  .contact {
    position: absolute; left: 312px; top: 96px;
    color: var(--ink-grey);
  }
  .contact__name {
    font-size: 17px; font-weight: 700; color: var(--brand-red); line-height: 1.1;
  }
  .contact__title { font-size: 11.5px; margin-bottom: 14px; }
  .contact__row {
    display: flex; align-items: flex-start; gap: 7px;
    font-size: 11.5px; line-height: 1.35; margin-bottom: 3px;
  }
  .contact__icon { flex: none; margin-top: 2px; }
</style>
</head>
<body>
<div class="canvas">
  <section class="card card--front">
    <div class="brand">
      <span class="brand__dot"></span>
      <span class="brand__name">quorva</span>
    </div>
    <div class="divider"></div>
    <div class="contact">
      <p class="contact__name">Daniel Rourke</p>
      <p class="contact__title">Managing Director</p>
      <p class="contact__row">
        <svg class="contact__icon" width="11" height="11" viewBox="0 0 12 12" aria-hidden="true">
          <circle cx="6" cy="6" r="6" fill="#b5121b"/>
          <path d="M3.6 3.2c.4-.3.8-.2 1 .2l.5 1c.1.3 0 .5-.2.7l-.3.3c.3.7.9 1.3 1.6 1.6l.3-.3c.2-.2.4-.3.7-.2l1 .5c.4.2.5.6.2 1-.5.6-1.2.8-1.9.5C5 7.9 4 6.9 3.4 5.5c-.3-.7-.3-1.7.2-2.3z" fill="#fff"/>
        </svg>
        <span>555 014 7396</span>
      </p>
      <p class="contact__row">
        <svg class="contact__icon" width="11" height="11" viewBox="0 0 12 12" aria-hidden="true">
          <circle cx="6" cy="6" r="6" fill="#b5121b"/>
          <rect x="3" y="3.8" width="6" height="4.4" rx=".6" fill="#fff"/>
          <path d="M3.3 4.2 6 6.3l2.7-2.1" stroke="#b5121b" stroke-width=".8" fill="none"/>
        </svg>
        <span>hello@quorvamail.com</span>
      </p>
      <p class="contact__row">
        <svg class="contact__icon" width="11" height="11" viewBox="0 0 12 12" aria-hidden="true">
          <circle cx="6" cy="6" r="6" fill="#b5121b"/>
          <path d="M6 2.6a2.3 2.3 0 0 0-2.3 2.3C3.7 6.6 6 9.4 6 9.4s2.3-2.8 2.3-4.5A2.3 2.3 0 0 0 6 2.6z" fill="#fff"/>
          <circle cx="6" cy="4.9" r=".9" fill="#b5121b"/>
        </svg>
        <span>4172 Marlowe blvd,<br>Alder Vale, NV 89412</span>
      </p>
    </div>
  </section>

  <section class="card card--back" role="img" aria-label="Card back: red field with an embossed tone-on-tone geometric pattern"></section>
</div>
</body>
</html>
```